All-Natural Head Lice Removal company

I need a business card with my pre-existing logo. We are a new company located in Portland Oregon that goes into peoples homes to help with head lice removal. My products and approach are all- natural and also will be around children.On my current logo we used Teal Bl and the color Green. I am open to new ideas just want it simple and creative

Target Market(s)

my biggest market is families of school aged children

Industry/Entity Type

Business

Contact Information for Business Card

see upload for details from previous business card

Font styles to use
Serif

Colors
33a6d7
9bcb3b
f37122

Requirements
Must have
• Basic information/ logo put into a creative format that is catching to the eye
Nice to have
• creative

```html
<!DOCTYPE html>
<html lang="en">
<head>
<meta charset="utf-8">
<title>Bright Nest Business Card</title>
<link rel="stylesheet" href="https://fonts.googleapis.com/css2?family=Arvo:wght@400;700&display=swap">
<style>
  :root {
    --sky-light: #8fd6f3;
    --sky: #4fb3e6;
    --sky-deep: #1f86cf;
    --ink: #151517;
    --ink-soft: #2a2b2e;
    --leaf: #8cc63f;
    --white: #ffffff;
    --text-dark: #1b1d22;
    --backdrop: #eef1f4;
  }
  * { box-sizing: border-box; margin: 0; padding: 0; }
  html, body { width: 1200px; height: 913px; overflow: hidden; }
  body {
    background: var(--backdrop);
    font-family: "Arvo", Georgia, serif;
    position: relative;
  }
  .card {
    position: absolute;
    width: 525px;
    height: 300px;
    overflow: hidden;
    background: linear-gradient(180deg, var(--sky-light) 0%, var(--sky) 55%, var(--sky-deep) 100%);
    box-shadow: 0 10px 30px rgba(0,0,0,.18);
  }
  .card--front { left: 50px; top: 180px; }
  .card--back { left: 625px; top: 433px; }
  .card__band { position: absolute; inset: 0; width: 100%; height: 100%; }

  .tagline-top {
    position: absolute; left: 22px; top: 22px;
    display: flex; align-items: center; gap: 10px;
    font-size: 15px; color: var(--text-dark);
  }
  .tagline-top__square { width: 16px; height: 12px; background: var(--white); }

  .brand {
    position: absolute;
    display: flex; align-items: center; gap: 10px;
    font-weight: 700; color: var(--ink);
    white-space: nowrap;
  }
  .brand__dot { border-radius: 50%; background: var(--leaf); flex: none; }
  .card--front .brand { right: 30px; top: 122px; font-size: 30px; color: var(--white); }
  .card--front .brand__dot { width: 30px; height: 30px; }
  .card--back .brand { left: 0; right: 0; justify-content: center; top: 60px; font-size: 40px; }
  .card--back .brand__dot { width: 40px; height: 40px; }

  .contact {
    position: absolute; left: 26px; bottom: 22px;
    color: var(--white);
  }
  .contact__name { font-size: 20px; letter-spacing: .5px; text-transform: uppercase; }
  .contact__role { font-size: 12px; color: var(--sky); text-transform: uppercase; margin: 2px 0 6px; }
  .contact__line { display: flex; align-items: center; gap: 8px; font-size: 13px; line-height: 19px; }
  .contact__icon { width: 12px; height: 12px; flex: none; }

  .slogan {
    position: absolute; left: 0; right: 0; top: 150px;
    text-align: center; font-size: 14.5px; line-height: 19px; color: var(--text-dark);
  }
  .web-strip {
    position: absolute; left: 0; right: 0; top: 212px;
    text-align: center; font-size: 14px; color: var(--white); font-weight: 700;
  }
</style>
</head>
<body>

  <section class="card card--front" aria-label="Business card front">
    <svg class="card__band" viewBox="0 0 525 300" preserveAspectRatio="none" aria-hidden="true">
      <polygon points="0,178 525,62 525,300 0,300" fill="var(--ink)"/>
      <polyline points="0,172 525,56" stroke="var(--white)" stroke-width="2" fill="none"/>
      <polyline points="0,178 525,62" stroke="var(--sky)" stroke-width="3" fill="none"/>
    </svg>
    <div class="tagline-top"><span class="tagline-top__square"></span>All Natural In-Home Lice Removal Services</div>
    <div class="brand"><span class="brand__dot"></span>Bright Nest</div>
    <div class="contact">
      <p class="contact__name">Maren Holloway</p>
      <p class="contact__role">Owner</p>
      <p class="contact__line">
        <svg class="contact__icon" viewBox="0 0 12 12" aria-hidden="true"><path d="M3 1 L5 3 L4 4.5 Q5 7 7.5 8 L9 7 L11 9 L9.5 11 Q3 10 1 3 Z" fill="var(--sky)"/></svg>
        1-855-555-NITS (6487)
      </p>
      <p class="contact__line">
        <svg class="contact__icon" viewBox="0 0 12 12" aria-hidden="true"><rect x="1" y="2.5" width="10" height="7" fill="none" stroke="var(--sky)" stroke-width="1.2"/><polyline points="1,2.5 6,6.5 11,2.5" fill="none" stroke="var(--sky)" stroke-width="1.2"/></svg>
        maren@brightnest.com
      </p>
      <p class="contact__line">
        <svg class="contact__icon" viewBox="0 0 12 12" aria-hidden="true"><circle cx="6" cy="6" r="5" fill="none" stroke="var(--sky)" stroke-width="1.2"/><ellipse cx="6" cy="6" rx="2.2" ry="5" fill="none" stroke="var(--sky)" stroke-width="1"/><line x1="1" y1="6" x2="11" y2="6" stroke="var(--sky)" stroke-width="1"/></svg>
        www.brightnest.com
      </p>
    </div>
  </section>

  <section class="card card--back" aria-label="Business card back">
    <svg class="card__band" viewBox="0 0 525 300" preserveAspectRatio="none" aria-hidden="true">
      <polygon points="0,200 525,200 525,240 0,240" fill="var(--ink)"/>
      <polygon points="0,240 525,240 525,244 0,244" fill="var(--ink-soft)"/>
    </svg>
    <div class="brand"><span class="brand__dot"></span>Bright Nest</div>
    <p class="slogan">Try Bright Nest Today and Be Lice Free Tomorrow!<br>All Natural In-Home Lice Removal Services</p>
    <p class="web-strip">www.brightnest.com</p>
  </section>

</body>
</html>
```